Homemaking training schools needs a Business Card design

Designer, Hello!

No special requirements, good-looking enough.
--------------------------------------------------------------------------

Name: Marcus Dole
Chairman
Tel: 0574-71948263
Mobile: 13857420916
Email: kelvora@mailnest.example
Web: www.prt2019.example
Add: No.258, LanpingJie, BeiyuanQu, Ningbo, Zhejiang

LOGO
Ningbo PRT Homemaking Training School

Target Market(s)

pregnant women, mothers, infants, the elderly and families, including cleaning, cooking, nursing training.

Industry/Entity Type

Business

Contact Information for Business Card

Name: Marcus Dole
Chairman
Tel: 0574-71948263
Mobile: 13857420916
Email: kelvora@mailnest.example
Web: www.prt2019.example

LOGO

Font styles to use
Serif
Sans Serif
Decorative

Requirements
Nice to have
• Feels: clean, specifications, safety, comfort, warmth and happiness.

```html
<!DOCTYPE html>
<html lang="en">
<head>
<meta charset="utf-8">
<title>PeiRenTang Business Card</title>
<link href="https://fonts.googleapis.com/css2?family=Poppins:wght@300;400;500;600&display=swap" rel="stylesheet">
<style>
  :root{
    --magenta:#e8158f;
    --blue:#2a86c8;
    --blue-deep:#1f74b5;
    --white:#ffffff;
    --ink:#4a4a4a;
    --stage:#eeeae4;
  }
  *{margin:0;padding:0;box-sizing:border-box}
  html,body{width:1200px;height:950px;overflow:hidden;background:var(--stage);font-family:'Poppins',sans-serif}
  .canvas{position:relative;width:1200px;height:950px}
  .card{position:absolute;left:300px;width:600px;height:360px;overflow:hidden;border-radius:4px;box-shadow:0 6px 18px rgba(0,0,0,.15)}
  .card-front{top:90px;background:var(--magenta);color:var(--white)}
  .card-back{top:500px;background:var(--white)}

  .front-brand{position:absolute;left:0;right:0;top:110px;text-align:center}
  .front-brand .brand-name{font-size:46px;font-weight:500;letter-spacing:.5px;display:inline-flex;align-items:center;gap:12px}
  .brand-dot{display:inline-block;width:14px;height:14px;border-radius:50%;background:currentColor}
  .front-brand .tagline{font-size:17px;font-weight:300;margin-top:2px}
  .front-brand .rule{width:250px;height:1px;background:var(--white);margin:8px auto 0}
  .front-web{position:absolute;left:0;right:0;top:262px;text-align:center;font-size:14px;letter-spacing:6px;font-weight:300}

  .back-panel{position:absolute;inset:0}
  .person{position:absolute;right:34px;top:34px;text-align:right}
  .person .name{color:var(--magenta);font-size:22px;font-weight:600;line-height:1.1}
  .person .role{color:var(--white);font-size:14px;font-weight:300;margin-top:2px}
  .address{position:absolute;right:34px;top:112px;text-align:right;color:var(--white);font-size:13px;line-height:1.45;font-weight:300}
  .contacts{position:absolute;right:22px;top:196px;list-style:none;color:var(--white);font-size:13.5px;font-weight:300}
  .contacts li{display:flex;justify-content:flex-end;align-items:center;gap:8px;height:22px}
  .icon{width:15px;height:15px;flex:none}

  .back-brand{position:absolute;left:40px;top:250px}
  .back-brand .brand-name{color:var(--blue);font-size:36px;font-weight:500;display:flex;align-items:center;gap:10px}
  .back-brand .brand-dot{width:12px;height:12px;background:var(--magenta)}
  .back-brand .tagline{color:var(--ink);font-size:13px;font-weight:300;margin-left:62px}
  .back-brand .rule{width:240px;height:1px;background:var(--ink);margin-top:6px}
</style>
</head>
<body>
<main class="canvas">
  <section class="card card-front" aria-label="Card front">
    <div class="front-brand">
      <div class="brand-name"><span class="brand-dot"></span>PeiRenTang</div>
      <div class="tagline">Training &amp; Services</div>
      <div class="rule"></div>
    </div>
    <div class="front-web">www.prt2019.example</div>
  </section>

  <section class="card card-back" aria-label="Card back">
    <svg class="back-panel" width="600" height="360" viewBox="0 0 600 360" aria-hidden="true">
      <path d="M600 0 H330 C260 40 250 110 290 160 C340 230 370 290 420 360 H600 Z" fill="var(--blue)"/>
      <path d="M330 0 C280 30 270 90 300 140" fill="none" stroke="var(--blue-deep)" stroke-width="2" opacity=".4"/>
    </svg>

    <div class="person">
      <div class="name">Marcus Dole</div>
      <div class="role">Chairman</div>
    </div>
    <div class="address">No.258, LanpingJie<br>BeiyuanQu, Ningbo<br>Zhejiang</div>

    <ul class="contacts">
      <li>0574-71948263
        <svg class="icon" viewBox="0 0 16 16"><circle cx="8" cy="8" r="8" fill="var(--magenta)"/><path d="M5 4.5l1.6-.5 1 2-1 .8c.4 1 1.1 1.7 2 2.1l.8-1 2 1-.5 1.6c-3 .2-6-2.8-5.9-6z" fill="#fff"/></svg></li>
      <li>13857420916
        <svg class="icon" viewBox="0 0 16 16"><circle cx="8" cy="8" r="8" fill="var(--magenta)"/><rect x="5.5" y="3.5" width="5" height="9" rx="1" fill="#fff"/><rect x="6.3" y="4.6" width="3.4" height="6" fill="var(--magenta)"/></svg></li>
      <li>kelvora@mailnest.example
        <svg class="icon" viewBox="0 0 16 16"><circle cx="8" cy="8" r="8" fill="var(--magenta)"/><rect x="4" y="5" width="8" height="6" fill="#fff"/><path d="M4 5l4 3.2L12 5" fill="none" stroke="var(--magenta)" stroke-width="1"/></svg></li>
      <li>www.prt2019.example
        <svg class="icon" viewBox="0 0 16 16"><circle cx="8" cy="8" r="8" fill="var(--magenta)"/><circle cx="8" cy="8" r="4" fill="none" stroke="#fff" stroke-width="1.1"/><path d="M4 8h8M8 4c-2 2.5-2 5.5 0 8M8 4c2 2.5 2 5.5 0 8" fill="none" stroke="#fff" stroke-width=".9"/></svg></li>
    </ul>

    <div class="back-brand">
      <div class="brand-name"><span class="brand-dot"></span>PeiRenTang</div>
      <div class="tagline">Training &amp; Services</div>
      <div class="rule"></div>
    </div>
  </section>
</main>
</body>
</html>
```